Corvina Dental personal information forms

We are a Dental Practice that require an update to our information forms, there are 3 versions of it.
I will attach our old ones, we need to keep the same information on there, we just want them to look better and use our current logo and colours.
Our website is www.corvinadental.net
Our facebook is www.friendspage.net/corvinadentalbelmorewalk/
..................................................................................................

Target Market(s)

Everyone, easy to read

Industry/Entity Type

Dental Clinic

Colors
0692cd
34a6d7
cee9f5
ffffff
0255a3
3276b5

Requirements
Must have
• Logo
• Our colours
• same information as the uploaded versions
Should not have
• any other colour besides the blues, black and white

```html
<!DOCTYPE html>
<html lang="en">
<head>
<meta charset="utf-8">
<title>Corvina Dental – New Patient Form pg. 2</title>
<link href="https://fonts.googleapis.com/css2?family=Mulish:ital,wght@0,400;0,500;0,700;0,800;1,400;1,700&display=swap" rel="stylesheet">
<style>
  :root{
    --blue:#0692cd;
    --sky:#34a6d7;
    --mist:#cee9f5;
    --white:#ffffff;
    --navy:#0255a3;
    --steel:#3276b5;
    --ink:#1a1a1a;
    --rule:#5a5a5a;
  }
  html,body{margin:0;padding:0;overflow:hidden;}
  body{width:729px;height:1200px;font-family:"Mulish",sans-serif;color:var(--ink);}
  .page{
    position:relative;width:729px;height:1200px;overflow:hidden;
    background:linear-gradient(to bottom,var(--white) 0%,var(--white) 78%,var(--mist) 100%);
  }
  .header-band{
    position:absolute;left:0;top:0;width:729px;height:170px;
    background:
      linear-gradient(to bottom,rgba(255,255,255,0) 0%,rgba(255,255,255,0) 60%,var(--white) 100%),
      linear-gradient(100deg,#b9dcef 0%,#e4f2fa 55%,var(--white) 100%);
  }
  .brand{
    position:absolute;right:22px;top:40px;margin:0;
    font-family:"Mulish",sans-serif;font-weight:500;font-size:46px;
    letter-spacing:-0.5px;color:var(--blue);line-height:1;
  }
  .el{position:absolute;margin:0;}
  .surgeons{left:22px;top:182px;font-style:italic;font-size:19.5px;line-height:26px;color:var(--blue);font-weight:400;}
  .form-tag{right:22px;top:211px;font-size:11px;letter-spacing:0.4px;color:var(--blue);}
  .form-tag b{font-size:16px;font-weight:800;color:var(--blue);margin-left:3px;}
  .welcome{left:22px;top:258px;font-size:17.5px;font-weight:500;color:var(--blue);letter-spacing:0.2px;}
  .intro{left:22px;top:284px;width:690px;font-size:13.2px;line-height:18.5px;}
  .section-lead{left:22px;width:690px;font-size:12.6px;line-height:17px;}
  .section-lead b{font-weight:800;}
  .q{left:22px;font-size:12.8px;}
  .yn{right:22px;font-size:12.8px;font-weight:800;}
  .rule{position:absolute;left:22px;right:22px;height:0;border-top:1px solid var(--rule);}
  .opt{position:absolute;font-size:12.8px;white-space:nowrap;}
  .box{display:inline-block;width:8px;height:8px;border:1px solid #555;margin-right:8px;vertical-align:0px;}
  .opt.lg{font-size:14px;}
  .legal{left:22px;top:1050px;width:688px;font-size:11.2px;line-height:15.7px;}
  .legal em{font-weight:700;}
  .sign{left:22px;top:1166px;font-size:12.8px;}
</style>
</head>
<body>
<div class="page">

  <div class="header-band" role="img" aria-label="Soft blue header band with flowing wave decoration"></div>

  <p class="brand">Corvina Dental</p>

  <p class="el surgeons">Dr. Stefan Korvalis &amp; Dr. Graham Whitby<br>Dental Surgeons</p>
  <p class="el form-tag">NEW PATIENT FORM <b>pg. 2</b></p>

  <h1 class="el welcome">WELCOME TO OUR PRACTICE!</h1>
  <p class="el intro">It is <b><i>essential</i></b> that we know about your past and present medical history. Many medical conditions may interfere with dental procedures. Please take your time and thoroughly complete the following section.</p>

  <p class="el section-lead" style="top:339px"><b>DENTAL HISTORY</b>—Are you concerned about or experiencing any of the following dental problems? (Please tick as many as applies).</p>

  <span class="opt" style="left:27px;top:383px"><span class="box"></span>Sensitivity to hot/cold</span>
  <span class="opt" style="left:259px;top:383px"><span class="box"></span>Food trapping between teeth</span>
  <span class="opt" style="left:487px;top:383px"><span class="box"></span>Clicking/pain in the jaw joints</span>
  <span class="opt" style="left:27px;top:405px"><span class="box"></span>Staining of your teeth</span>
  <span class="opt" style="left:259px;top:405px"><span class="box"></span>Discoloured fillings</span>
  <span class="opt" style="left:487px;top:405px"><span class="box"></span>Roughness of existing fillings</span>
  <span class="opt" style="left:27px;top:427px"><span class="box"></span>Bleeding gums</span>
  <span class="opt" style="left:259px;top:427px"><span class="box"></span>Bad breath</span>
  <span class="opt" style="left:487px;top:427px"><span class="box"></span>Tenderness when eating</span>
  <span class="opt" style="left:27px;top:450px"><span class="box"></span>Crowding of teeth</span>
  <span class="opt" style="left:259px;top:450px"><span class="box"></span>Grinding/Clenching of teeth</span>
  <span class="opt" style="left:487px;top:450px"><span class="box"></span>Poorly fitted crowns/dentures</span>

  <p class="el q" style="top:476px">What is the main purpose of your visit today?</p>
  <div class="rule" style="top:507px"></div>
  <p class="el q" style="top:514px">How long has it been since your last dental visit?</p>
  <div class="rule" style="top:545px"></div>
  <p class="el q" style="top:553px">Does dental treatment make you nervous?</p>

  <span class="opt lg" style="left:27px;top:577px"><span class="box"></span>No</span>
  <span class="opt lg" style="left:198px;top:577px"><span class="box"></span>Slightly</span>
  <span class="opt lg" style="left:371px;top:577px"><span class="box"></span>Moderately</span>
  <span class="opt lg" style="left:540px;top:577px"><span class="box"></span>Extremely</span>

  <p class="el q" style="top:601px;font-weight:800;font-size:13.2px">MEDICAL HISTORY</p>
  <p class="el q" style="top:626px;left:27px">Name of Family Doctor (GP):</p>
  <div class="rule" style="top:645px"></div>
  <p class="el q" style="top:650px;left:27px">Clinic</p>
  <p class="el q" style="top:650px;left:369px">Phone:</p>
  <div class="rule" style="top:672px"></div>

  <p class="el q" style="top:676px">Have you taken any prescribed medication or dietary supplements in the last 12 months?</p>
  <p class="el q" style="top:696px">(If yes, please list below.)</p>
  <p class="el yn" style="top:696px">YES/NO</p>
  <div class="rule" style="top:730px"></div>
  <p class="el q" style="top:733px">Allergies/Reactions? If yes, please list below.</p>
  <p class="el yn" style="top:733px">YES/NO</p>
  <div class="rule" style="top:766px"></div>

  <p class="el q" style="top:775px">Have you <b>ever had</b> or are you <b>suffering</b> from any of the following? Please tick any that apply:</p>

  <span class="opt" style="left:27px;top:797px"><span class="box"></span>Rheumatic fever</span>
  <span class="opt" style="left:198px;top:797px"><span class="box"></span>Hepatitis A B or C</span>
  <span class="opt" style="left:371px;top:797px"><span class="box"></span>Artificial joints</span>
  <span class="opt" style="left:542px;top:797px"><span class="box"></span>Osteoporosis</span>
  <span class="opt" style="left:27px;top:819px"><span class="box"></span>Epilepsy</span>
  <span class="opt" style="left:198px;top:819px"><span class="box"></span>Diabetes</span>
  <span class="opt" style="left:371px;top:819px"><span class="box"></span>Respiratory problems</span>
  <span class="opt" style="left:542px;top:819px"><span class="box"></span>Heart rate problems</span>
  <span class="opt" style="left:27px;top:841px"><span class="box"></span>Asthma</span>
  <span class="opt" style="left:198px;top:841px"><span class="box"></span>Kidney Disease</span>
  <span class="opt" style="left:371px;top:841px"><span class="box"></span>HIV Positive</span>
  <span class="opt" style="left:542px;top:841px"><span class="box"></span>Heart murmur</span>
  <span class="opt" style="left:27px;top:864px"><span class="box"></span>Tuberculosis</span>
  <span class="opt" style="left:198px;top:864px"><span class="box"></span>Heart Attack</span>
  <span class="opt" style="left:371px;top:864px"><span class="box"></span>High Cholesterol</span>
  <span class="opt" style="left:27px;top:887px"><span class="box"></span>Radiation Therapy</span>
  <span class="opt" style="left:198px;top:887px"><span class="box"></span>High Blood Pressure</span>
  <span class="opt" style="left:371px;top:887px"><span class="box"></span>Cancer</span>
  <span class="opt" style="left:27px;top:909px"><span class="box"></span>Dizziness, fainting</span>
  <span class="opt" style="left:198px;top:909px"><span class="box"></span>Bleeding problems</span>
  <span class="opt" style="left:371px;top:909px"><span class="box"></span>Pace-maker</span>

  <p class="el q" style="top:929px">Do you have any disease, condition or problem not listed above? (If yes, please give details).</p>
  <p class="el yn" style="top:929px">YES/NO</p>
  <div class="rule" style="top:957px"></div>
  <p class="el q" style="top:968px">Have you had surgery or been to hospital in the last 5 years? (If yes, please give details).</p>
  <p class="el yn" style="top:968px">YES/NO</p>
  <div class="rule" style="top:997px"></div>
  <p class="el q" style="top:1009px">For women: Are you pregnant? If yes, how many months?</p>
  <p class="el yn" style="top:1009px">YES/NO</p>
  <div class="rule" style="top:1040px"></div>

  <p class="el legal"><em><i>The information above that I have provided is to the best of my knowledge true and correct and I understand that it is my responsibility to inform of any changes in my medical status.</i></em><i> This is to certify that I, the undersigned, consent to the performing of the dental and oral surgery procedures agreed to be necessary or advisable, including the use of local anaesthetic as indicated and I will assume responsibility for the fees associated with these procedures. Therefore, I shall pay any legal costs, including solicitor and own costs, tracing costs and any collection commission incurred by Corvina Dental as a result of my failure to pay any amount due to Corvina Dental.</i></p>

  <p class="el sign">Patient/Parent/Person Responsible Signature:_______________________________________ Date:____________________</p>

</div>
</body>
</html>
```